Refresh Brightpath Coursecraft

Need a new design for e-learning development and web app development site: http://brightpathcoursecraft.example. Need pages for everything on menu bar plus a training services and a web app development services pages and a better page for samples http://brightpathcoursecraft.example/samples5/.

***Must be programmed in html 5. NO CMS. No WP. No Plume. Straight html/css.

Target Market(s)

government

Industry/Entity Type

Government

Coding

Coded - Design and coding required

Number of Pages Required

1 page

Requirements
Must have
• Must be coded in html5/css. No CMS.
• Divided so you can easily see that we offer 3 separate services:
• Live Training - E-Learning Development - Web App Development
• A way to display logos of all our clients like on bottom of this page: https://www.quorvatests.example (this is also our website so you can copy all these logos)
• List both our Denver location which is already on our website plus our office in Velmoro Plaza. Street 62 Sur, 14-87. Medellín, Antioquia.
• A page like this for our web app dev services https://www.tekvanu.example/product-development
Should not have
• CMS

```html
<!DOCTYPE html>
<html lang="en">
<head>
<meta charset="utf-8">
<title>Brightpath Coursecraft</title>
<link rel="stylesheet" href="https://fonts.googleapis.com/css2?family=Montserrat:wght@400;500;600;700&display=swap">
<style>
:root{
  --blue:#1a87c4;
  --blue-deep:#1778b0;
  --orange:#f3a21c;
  --ink:#1d1d1d;
  --body:#4a4a4a;
  --grey-bg:#ededed;
  --footer:#262626;
  --footer-text:#d6d6d6;
  --white:#fff;
}
*{box-sizing:border-box;margin:0;padding:0}
html,body{width:1200px;height:3830px;overflow:hidden}
body{font-family:"Montserrat",sans-serif;color:var(--body);background:var(--white);position:relative}
a{color:inherit;text-decoration:none}

.site-header{position:absolute;top:0;left:0;width:1200px;height:85px;background:var(--white);display:flex;align-items:center;justify-content:space-between;padding:0 120px 0 125px}
.brand{display:flex;align-items:center;gap:12px;color:var(--orange);font-weight:600;font-size:20px;letter-spacing:.5px}
.brand-dot{width:40px;height:40px;border-radius:50%;background:var(--orange)}
.main-nav{display:flex;gap:30px;font-size:15px;font-weight:600;color:var(--ink);letter-spacing:.3px}

.hero{position:absolute;top:85px;left:0;width:1200px;height:555px;background:linear-gradient(100deg,#6d6f72 0%,#8c8e90 35%,#4c4a48 70%,#2f2b29 100%)}
.hero-title{position:absolute;top:210px;left:0;width:1200px;text-align:center;color:var(--white);font-size:40px;font-weight:600;line-height:1.3;letter-spacing:.5px}
.hero-dots{position:absolute;right:40px;top:235px;display:flex;flex-direction:column;gap:14px;align-items:center}
.hero-dots span{width:12px;height:12px;border-radius:50%;background:var(--white)}
.hero-dots span.active{width:26px;height:26px;border:3px solid var(--white);background:transparent;position:relative}
.hero-dots span.active::after{content:"";position:absolute;inset:5px;border-radius:50%;background:var(--white)}

.section-mark{width:70px;height:70px;border-radius:50%;background:var(--orange);margin:0 auto}
.section-title{text-align:center;color:var(--blue);font-size:40px;font-weight:600;letter-spacing:1px;margin-top:20px}

.about{position:absolute;top:640px;left:0;width:1200px;height:523px;padding-top:55px}
.about-text{width:830px;margin:30px auto 0;text-align:center;font-size:14.5px;line-height:2.2;color:var(--ink)}
.about-text .highlight{color:var(--blue-deep)}
.btn-outline{display:block;width:150px;height:42px;margin:30px auto 0;border:2px solid var(--ink);border-radius:3px;text-align:center;line-height:38px;font-size:15px;font-weight:600;color:var(--ink)}

.services{position:absolute;top:1163px;left:0;width:1200px;height:1639px;background:var(--grey-bg);padding-top:55px}
.service{position:absolute;left:0;width:1200px;height:360px}
.service-body{position:absolute;top:0;width:490px}
.service-title{font-size:33px;font-weight:600;color:var(--ink);letter-spacing:.5px}
.service-text{margin-top:22px;font-size:15px;line-height:1.95;color:var(--body)}
.btn-solid{display:inline-block;margin-top:32px;width:162px;height:52px;background:var(--blue);color:var(--white);font-size:17px;font-weight:600;text-align:center;line-height:52px}
.service-photo-wrap{position:absolute;top:-18px;width:445px;height:345px}
.service-photo-backing{position:absolute;width:420px;height:320px;background:var(--blue-deep)}
.service-photo{position:absolute;top:0;width:425px;height:322px;border-radius:6px}
.service--right .service-body{left:113px}
.service--right .service-photo-wrap{left:663px}
.service--right .service-photo-backing{left:20px;top:25px}
.service--right .service-photo{left:0}
.service--left .service-body{left:598px}
.service--left .service-photo-wrap{left:95px}
.service--left .service-photo-backing{left:0;top:25px}
.service--left .service-photo{left:18px}
.photo-training{background:linear-gradient(135deg,#d9b27e 0%,#b9875a 40%,#e3ded6 75%,#9a7b5c 100%)}
.photo-elearning{background:linear-gradient(135deg,#e7e1d8 0%,#7a5e4c 45%,#c2a58c 80%,#5b4a40 100%)}
.photo-webapp{background:linear-gradient(135deg,#2f3d55 0%,#8a5f6a 45%,#d79b7b 75%,#3b4156 100%)}

.clients{position:absolute;top:2802px;left:0;width:1200px;height:614px;background:var(--white);padding-top:60px}
.clients .section-title{font-size:38px}
.client-row{position:absolute;left:110px;width:980px;display:flex;justify-content:space-between;align-items:center}
.client{display:flex;align-items:center;gap:6px;font-size:12px;font-weight:600;color:#3a4a66;max-width:120px;line-height:1.2}
.client i{flex:none;width:38px;height:38px;border-radius:50%;background:#c9ced8}

.site-footer{position:absolute;top:3416px;left:0;width:1200px;height:414px;background:var(--footer);color:var(--footer-text)}
.footer-col{position:absolute;top:40px}
.footer-heading{font-size:22px;font-weight:600;color:var(--white)}
.quick-links{list-style:none;margin-top:22px;font-size:13.5px;line-height:29px}
.quick-links li::before{content:"›";margin-right:14px;color:var(--footer-text)}
.social{display:flex;gap:10px;margin-top:14px}
.social span{width:22px;height:22px;border-radius:50%;border:1.5px solid var(--footer-text)}
.contact-list{list-style:none;margin-top:18px;font-size:12.5px;line-height:1.6}
.contact-list li{display:flex;gap:14px;margin-bottom:10px;width:250px}
.contact-list svg{flex:none;margin-top:3px}
.map{width:222px;height:112px;margin-top:10px;background:linear-gradient(135deg,#e4e7e2 0%,#d4dccf 50%,#e9e6de 100%)}
.footer-bottom{position:absolute;top:3755px;left:113px;width:975px;border-top:1px solid #4a4a4a;padding-top:26px;display:flex;justify-content:space-between;font-size:13px;color:var(--footer-text)}
.legal-links{display:flex;gap:40px}
</style>
</head>
<body>

<header class="site-header">
  <a class="brand" href="#"><span class="brand-dot"></span>Brightpath Coursecraft</a>
  <nav class="main-nav">
    <a href="#">HOME</a><a href="#">PORTFOLIO</a><a href="#">TEAM &amp; EXPERIENCE</a><a href="#">CONTACTS</a>
  </nav>
</header>

<section class="hero" role="img" aria-label="Learners working at computers in a bright training room">
  <h1 class="hero-title">WE CREATE ENGAGING TRAINING<br>THAT EXCEED EXPECTATIONS.</h1>
  <div class="hero-dots"><span class="active"></span><span></span><span></span></div>
</section>

<section class="about">
  <div class="section-mark"></div>
  <h2 class="section-title">ABOUT US</h2>
  <p class="about-text">Brightpath Coursecraft is a HUBZone Certified, SBA 8(a) Certified, Native American Owned Small Disadvantaged Business located in Denver, Colorado. We have designed and delivered <span class="highlight">SCORM compliant eLearning, webinar, web-based training (WBT), instructor-led training (ILT), virtual ILT (vILT), blended, and 3D Immersive training courses.</span> The Instructional Design Team brings nearly one hundred years of Instructional Design experience. Our Instructional Designers have experience designing, developing, and delivering custom technical and business skill training courses.</p>
  <a class="btn-outline" href="#">Read More</a>
</section>

<section class="services">
  <div class="section-mark"></div>
  <h2 class="section-title">OUR SERVICES</h2>

  <article class="service service--right" style="top:277px">
    <div class="service-body">
      <h3 class="service-title">Live Training</h3>
      <p class="service-text">Lorem ipsum dolor sit amet, consectetur adipiscing elit, sed do eiusmod tempor incididunt ut labore et dolore magna aliqua. Ut enim ad minim veniam, quis nostrud exercitation ullamco laboris nisi ut aliquip ex ea commodo consequat. Duis aute irure dolor in reprehenderit in voluptate velit esse cillum dolore eu fugiat nulla pariatur.</p>
      <a class="btn-solid" href="#">Read More</a>
    </div>
    <div class="service-photo-wrap">
      <div class="service-photo-backing"></div>
      <div class="service-photo photo-training" role="img" aria-label="Trainer with headset leading a live session from a laptop"></div>
    </div>
  </article>

  <article class="service service--left" style="top:731px">
    <div class="service-body">
      <h3 class="service-title">E-Learning Development</h3>
      <p class="service-text">Lorem ipsum dolor sit amet, consectetur adipiscing elit, sed do eiusmod tempor incididunt ut labore et dolore magna aliqua. Ut enim ad minim veniam, quis nostrud exercitation ullamco laboris nisi ut aliquip ex ea commodo consequat. Duis aute irure dolor in reprehenderit in voluptate velit esse cillum dolore eu fugiat nulla pariatur.</p>
      <a class="btn-solid" href="#">Read More</a>
    </div>
    <div class="service-photo-wrap">
      <div class="service-photo-backing"></div>
      <div class="service-photo photo-elearning" role="img" aria-label="Students studying together at a laptop"></div>
    </div>
  </article>

  <article class="service service--right" style="top:1185px">
    <div class="service-body">
      <h3 class="service-title">Web App Development</h3>
      <p class="service-text">Lorem ipsum dolor sit amet, consectetur adipiscing elit, sed do eiusmod tempor incididunt ut labore et dolore magna aliqua. Ut enim ad minim veniam, quis nostrud exercitation ullamco laboris nisi ut aliquip ex ea commodo consequat. Duis aute irure dolor in reprehenderit in voluptate velit esse cillum dolore eu fugiat nulla pariatur.</p>
      <a class="btn-solid" href="#">Read More</a>
    </div>
    <div class="service-photo-wrap">
      <div class="service-photo-backing"></div>
      <div class="service-photo photo-webapp" role="img" aria-label="Hand holding a tablet with floating app icons"></div>
    </div>
  </article>
</section>

<section class="clients">
  <div class="section-mark"></div>
  <h2 class="section-title">A FEW OF OUR 75,000 CLIENTS</h2>
  <div class="client-row" style="top:270px">
    <span class="client"><i></i>Aerowing Corps</span>
    <span class="client"><i></i>Kestrel Valley</span>
    <span class="client"><i></i>Harlow College</span>
    <span class="client"><i></i>Ridgefield</span>
    <span class="client"><i></i>Ostrava Inst.</span>
    <span class="client">Stelvane</span>
    <span class="client"><i></i>Sunmire</span>
    <span class="client">Redcliff Labs</span>
  </div>
  <div class="client-row" style="top:368px">
    <span class="client"><i></i>Norhaven</span>
    <span class="client"><i></i>Calderbridge</span>
    <span class="client"><i></i>Larkwood University</span>
    <span class="client">Biovance Composites</span>
    <span class="client"><i></i>Pellam</span>
    <span class="client"><i></i>Thornfield</span>
  </div>
  <div class="client-row" style="top:466px">
    <span class="client"><i></i>Westmere</span>
    <span class="client"><i></i>Corvale State</span>
    <span class="client"><i></i>Granite Peak</span>
    <span class="client"><i></i>Harrowgate</span>
    <span class="client"><i></i>Emberline Fire</span>
    <span class="client"><i></i>Silverhill</span>
    <span class="client"><i></i>Ovarin</span>
  </div>
</section>

<footer class="site-footer">
  <div class="footer-col" style="left:136px">
    <h4 class="footer-heading">Quick Links</h4>
    <ul class="quick-links"><li>Home</li><li>Portfolio</li><li>Team &amp; Experience</li><li>Contacts</li></ul>
    <div class="social"><span></span><span></span><span></span><span></span></div>
  </div>
  <div class="footer-col" style="left:462px">
    <h4 class="footer-heading">Antioquia</h4>
    <ul class="contact-list">
      <li><svg width="10" height="13" viewBox="0 0 10 13"><path d="M5 0a5 5 0 0 0-5 5c0 4 5 8 5 8s5-4 5-8a5 5 0 0 0-5-5zm0 7a2 2 0 1 1 0-4 2 2 0 0 1 0 4z" fill="#d6d6d6"/></svg>Street 62 Sur, 14-87. Medellín, Antioquia.</li>
      <li><svg width="11" height="11" viewBox="0 0 11 11"><path d="M2 0l2 3-1 1.5c.7 1.5 2 2.8 3.5 3.5L8 7l3 2-1 2C5 11 0 6 0 1z" fill="#d6d6d6"/></svg>Phone : 555-014-2290</li>
      <li><svg width="12" height="9" viewBox="0 0 12 9"><rect width="12" height="9" fill="#d6d6d6"/><path d="M0 0l6 5 6-5" stroke="#262626" fill="none"/></svg>Email : support@quorvatests.example</li>
    </ul>
    <div class="map" role="img" aria-label="Street map of the Medellín office location"></div>
  </div>
  <div class="footer-col" style="left:830px">
    <h4 class="footer-heading">Aurora</h4>
    <ul class="contact-list">
      <li><svg width="10" height="13" viewBox="0 0 10 13"><path d="M5 0a5 5 0 0 0-5 5c0 4 5 8 5 8s5-4 5-8a5 5 0 0 0-5-5zm0 7a2 2 0 1 1 0-4 2 2 0 0 1 0 4z" fill="#d6d6d6"/></svg>5820 E Larkin Avenue, Suite 2-140 Aurora, CO 80019</li>
      <li><svg width="11" height="11" viewBox="0 0 11 11"><path d="M2 0l2 3-1 1.5c.7 1.5 2 2.8 3.5 3.5L8 7l3 2-1 2C5 11 0 6 0 1z" fill="#d6d6d6"/></svg>Phone : 555-014-2290</li>
      <li><svg width="12" height="9" viewBox="0 0 12 9"><rect width="12" height="9" fill="#d6d6d6"/><path d="M0 0l6 5 6-5" stroke="#262626" fill="none"/></svg>Email : support@quorvatests.example</li>
    </ul>
    <div class="map" role="img" aria-label="Street map of the Aurora office location"></div>
  </div>
</footer>
<div class="footer-bottom">
  <span>© Copyrights 2019 | All Rights Reserved</span>
  <span class="legal-links"><a href="#">Terms &amp; Conditions</a><a href="#">Privacy Policy</a><a href="#">Contact Us</a></span>
</div>

</body>
</html>
```